Business Cards Design for the electrical wholesaler: clean bold dynamic :)

We need a business card design that would follow our latest brand guidelines. As an electrical wholesaler we want to bring a fresh look and feel into the industry. The design should be clean bold and dynamic. It should come alive with the renewed energy of our green colour. Our grey colour should keep things balanced and complement the notion of maturity and responsibility. We employ Lato as a corporate font however are not bound by this font and we’re open to interpretation here.

Target Market(s)

Electrical contractors

Industry/Entity Type

Business

Contact Information for Business Card

Logo
Name & Surname: Halyna Dorosh
Job Title: Director of Marketing
Email: halya.dorosh@quillmail.example
Cell phone: 780.555.0172
Address: 20517 - 87 Ave. Edmonton, AB, Canada. T6K 4N8
Business Phone: 780.555.0184
Website: www.brovix.example

Font styles to use
Other font styles liked:
• Lato

Requirements
Must have
• Logo & website
Nice to have
• Brand elements - some of them you may find in the attached Brand Guidelines (e.g. three lines on the background signifying "W")

```html
<!DOCTYPE html>
<html lang="en">
<head>
<meta charset="utf-8">
<title>Brovix Electrical Wholesalers – Business Card</title>
<link href="https://fonts.googleapis.com/css2?family=Oswald:wght@600&family=Work+Sans:wght@400;500&display=swap" rel="stylesheet">
<style>
  :root {
    --stage: #161616;
    --card: #232323;
    --card-deep: #1b1b1b;
    --backdrop: #141414;
    --green: #7dc242;
    --white: #ffffff;
  }
  * { box-sizing: border-box; margin: 0; padding: 0; }
  html, body { width: 1200px; height: 900px; overflow: hidden; }
  body {
    background: var(--stage);
    font-family: "Work Sans", Arial, sans-serif;
    color: var(--white);
    position: relative;
  }
  .card {
    position: absolute;
    left: 250px;
    width: 700px;
    height: 400px;
    background: radial-gradient(ellipse at 45% 50%, #2b2b2b 0%, var(--card) 45%, var(--card-deep) 100%);
    overflow: hidden;
  }
  .card--front { top: 40px; }
  .card--back { top: 460px; }

  .brand-backdrop {
    position: absolute;
    left: 90px;
    top: 60px;
    width: 540px;
    height: 300px;
    border-radius: 40px;
    background: radial-gradient(ellipse at 30% 50%, var(--backdrop) 0%, rgba(20,20,20,0.55) 50%, rgba(20,20,20,0) 100%);
  }

  /* front */
  .brand {
    position: absolute;
    left: 170px;
    top: 120px;
  }
  .brand__row { display: flex; align-items: center; gap: 22px; }
  .brand__dot {
    width: 62px; height: 62px; border-radius: 50%;
    background: var(--green);
  }
  .brand__name {
    font-weight: 500;
    font-size: 92px;
    line-height: 1;
    color: var(--white);
    letter-spacing: 1px;
  }
  .brand__tagline {
    margin-top: 10px;
    margin-left: 86px;
    font-size: 15px;
    font-weight: 500;
    letter-spacing: 4px;
    text-transform: uppercase;
    color: var(--white);
  }

  /* back */
  .person {
    position: absolute;
    left: 20px;
    top: 128px;
    width: 330px;
    text-align: right;
  }
  .person__name {
    font-family: "Oswald", "Arial Narrow", sans-serif;
    font-weight: 600;
    font-size: 44px;
    line-height: 1;
    color: var(--green);
    text-transform: uppercase;
    letter-spacing: 1px;
    white-space: nowrap;
  }
  .person__role {
    margin-top: 8px;
    font-size: 19px;
    letter-spacing: 0.5px;
    color: var(--white);
    white-space: nowrap;
  }
  .divider {
    position: absolute;
    left: 368px;
    top: 118px;
    width: 2px;
    height: 114px;
    background: var(--green);
  }
  .contacts {
    position: absolute;
    left: 386px;
    top: 118px;
    list-style: none;
  }
  .contacts__item {
    display: flex;
    align-items: center;
    gap: 10px;
    font-size: 16px;
    letter-spacing: 0.5px;
    line-height: 28.5px;
    color: var(--white);
    white-space: nowrap;
  }
  .contacts__icon { width: 15px; height: 15px; flex: none; }
  .contacts__accent { color: var(--green); }
  .address {
    position: absolute;
    left: 60px;
    bottom: 60px;
    font-size: 19px;
    letter-spacing: 1.5px;
    color: var(--white);
    white-space: nowrap;
  }
</style>
</head>
<body>

<section class="card card--front" aria-label="Card front">
  <div class="brand-backdrop" role="img" aria-label="Faint brand backdrop"></div>
  <div class="brand">
    <div class="brand__row">
      <span class="brand__dot"></span>
      <span class="brand__name">brovix</span>
    </div>
    <p class="brand__tagline">Electrical Wholesalers</p>
  </div>
</section>

<section class="card card--back" aria-label="Card back">
  <div class="brand-backdrop" role="img" aria-label="Faint brand backdrop"></div>
  <div class="person">
    <h1 class="person__name">Halyna Dorosh</h1>
    <p class="person__role">Director of Marketing</p>
  </div>
  <span class="divider"></span>
  <ul class="contacts">
    <li class="contacts__item">
      <svg class="contacts__icon" viewBox="0 0 16 16" aria-hidden="true"><path d="M4 1.5 6 4.5 4.8 6c.8 2 2.4 3.6 4.4 4.4L10.7 9l3 2-1.2 2.8C7 13.5 2.5 9 2.2 3.2Z" fill="none" stroke="var(--green)" stroke-width="1.4" stroke-linejoin="round"/></svg>
      780.555.0184
    </li>
    <li class="contacts__item">
      <svg class="contacts__icon" viewBox="0 0 16 16" aria-hidden="true"><rect x="4" y="1" width="8" height="14" rx="1.5" fill="none" stroke="var(--green)" stroke-width="1.4"/><path d="M7 12.5h2" stroke="var(--green)" stroke-width="1.4"/></svg>
      780.555.0172
    </li>
    <li class="contacts__item">
      <svg class="contacts__icon" viewBox="0 0 16 16" aria-hidden="true"><rect x="1.5" y="3.5" width="13" height="9" fill="none" stroke="var(--green)" stroke-width="1.4"/><path d="M1.5 3.5 8 9l6.5-5.5" fill="none" stroke="var(--green)" stroke-width="1.4"/></svg>
      halya.dorosh@quillmail.example
    </li>
    <li class="contacts__item">
      <svg class="contacts__icon" viewBox="0 0 16 16" aria-hidden="true"><circle cx="8" cy="8" r="6.5" fill="none" stroke="var(--green)" stroke-width="1.3"/><ellipse cx="8" cy="8" rx="2.8" ry="6.5" fill="none" stroke="var(--green)" stroke-width="1.1"/><path d="M1.5 8h13M2.5 5h11M2.5 11h11" stroke="var(--green)" stroke-width="1"/></svg>
      <span>www.<span class="contacts__accent">brovix</span>.example</span>
    </li>
  </ul>
  <p class="address">20517 - 87 Ave. Edmonton, AB, Canada. T6K 4N8</p>
</section>

</body>
</html>
```